Full 10+ Page Online Learning eBook Design - NOT just the cover :)

We currently have an eBook within the online learning space which is geared towards a consumer audience (hobbyists, interests), but we have a new 2.0 version which is geared towards professionals (certifications, training, continuing ed, career-oriented). We need a new design and need the words/copy put into the eBook, but want to keep the look and feel of the original (open to variations in design). File is attached, along with various logo options.

Target Market(s)

Professionals

Industry/Entity Type

Learning

Font styles to use
Sans Serif

Colors
33a6d7
acd036
919191

Requirements
Must have
• Must follow a very similar look a feel of the original file. We use a lot of fonts like Raleway, Gotham, Helvetica Neue, Gil Sans, DIN - anything modern looking. We also use a lot of grayish hexagons in our corporate design. Feel free to check out brightlanternhub.example to get a better sense.
Nice to have
• Include some professionally oriented icons / photos
Should not have
• No cartoonish graphics or imagery

```html
<!DOCTYPE html>
<html lang="en">
<head>
<meta charset="utf-8">
<title>Four Questions – Bright Lantern Hub</title>
<link href="https://fonts.googleapis.com/css2?family=Raleway:wght@400;500&family=Montserrat:wght@400&display=swap" rel="stylesheet">
<style>
  :root {
    --brand-blue: #33a6d7;
    --brand-green: #acd036;
    --brand-gray: #919191;
    --ink: #111111;
    --paper: #ffffff;
  }
  * { margin: 0; padding: 0; box-sizing: border-box; }
  html, body { width: 852px; height: 1200px; overflow: hidden; background: var(--paper); }
  .page {
    position: relative;
    width: 852px;
    height: 1200px;
    overflow: hidden;
    background: var(--paper);
    font-family: "Raleway", "Helvetica Neue", Arial, sans-serif;
  }
  .hex-field { position: absolute; display: block; }
  .hex-field--blue {
    left: 0; top: 420px; width: 700px; height: 400px;
    background: radial-gradient(ellipse 70% 70% at 10% 20%, rgba(51,166,215,0.28), rgba(51,166,215,0.08) 60%, rgba(51,166,215,0) 100%);
  }
  .hex-field--green {
    left: 140px; top: 770px; width: 712px; height: 430px;
    background: radial-gradient(ellipse 75% 75% at 95% 90%, rgba(172,208,54,0.32), rgba(172,208,54,0.08) 60%, rgba(172,208,54,0) 100%);
  }
  .headline {
    position: absolute;
    left: 9px; top: 36px;
    font-family: "Raleway", "Helvetica Neue", Arial, sans-serif;
    font-weight: 500;
    font-size: 22.5px;
    line-height: 30px;
    color: var(--ink);
    white-space: nowrap;
  }
  .question-panel {
    position: absolute;
    left: 7px; top: 106px;
    width: 840px; height: 324px;
    background: var(--brand-blue);
    padding: 10px 10px 0 12px;
    color: var(--paper);
    font-family: "Montserrat", "Helvetica Neue", Arial, sans-serif;
    font-size: 15.6px;
    line-height: 20.4px;
  }
  .question-panel p { margin-bottom: 20.4px; }
  .question-panel .line { display: block; white-space: nowrap; }
  .contact {
    position: absolute;
    left: 0; top: 763px;
    width: 852px;
    text-align: center;
    font-family: "Raleway", "Helvetica Neue", Arial, sans-serif;
    font-size: 17px;
    line-height: 20.5px;
    color: #222;
  }
  .contact__lead { color: var(--ink); font-weight: 500; }
</style>
</head>
<body>
<main class="page">
  <div class="hex-field hex-field--blue" role="img" aria-label="Faint blue outline hexagon pattern fading to the right"></div>
  <div class="hex-field hex-field--green" role="img" aria-label="Faint green outline hexagon pattern fading to the upper left"></div>

  <h1 class="headline">If you're ready to claim your share of the explosive online learning industry,<br>it's time to ask yourself these four questions:</h1>

  <section class="question-panel">
    <p>
      <span class="line">Do you have the content? Whether that's videos, audio, multimedia, slideshows, images,</span>
      <span class="line">diagrams, whitepapers, articles or book content, it can all be converted into digital learning</span>
      <span class="line">objects that make up the body of your courses.</span>
    </p>
    <p>
      <span class="line">Do you have an audience? If you're already engaging with your users through online and</span>
      <span class="line">social channels, you've established an on-going relationship with them that positions you as a</span>
      <span class="line">trusted party for delivering the learning they want.</span>
    </p>
    <p>
      <span class="line">Do you have the right digital platform? Look beyond the functions of the standard learning</span>
      <span class="line">management system and take into consideration other essential features, such as content</span>
      <span class="line">management, ecommerce and reporting and tracking, which play a vital role in running a</span>
      <span class="line">profit-producing learning business.</span>
    </p>
    <p>
      <span class="line">Do you have the right partner? Bright Lantern Hub has experience in helping small, medium</span>
      <span class="line">and large companies in multiple industries monetize their learning assets.</span>
    </p>
  </section>

  <footer class="contact">
    <p class="contact__lead">To schedule a demo or speak with one of our learning business experts</p>
    <p>Call 1-800-555-0147</p>
    <p>Email explore@brightlanternhub.example</p>
  </footer>
</main>
</body>
</html>
```